MUSIC FESTIVAL 2023

On the occasion of the 2023 music festival, the 24th, brings the VELMORANTE group to its terrace.
We are organizing a giant barbecue on this occasion.
This event is organized in collaboration with LE BRUMAIRE.
Possibility of take-out!
Address of the event: 12-16 Rue Fernand Lavigne in CAMBRAI.4
From 19h.
03 41 58 62 19 - marc@orvaline-habitat.example
Please write in French.
To use the logos of the two establishments.

```html
<!DOCTYPE html>
<html lang="fr">
<head>
<meta charset="utf-8">
<title>Fête de la Musique 2023 – L'Escale</title>
<link rel="stylesheet" href="https://fonts.googleapis.com/css2?family=Poppins:wght@300;400;500;600;700&family=Jost:wght@400;500&family=Cormorant+Garamond:wght@500&display=swap">
<style>
  :root {
    --page: #ffffff;
    --ink: #0c0c0c;
    --ink-soft: #1d1d1d;
    --text: #ffffff;
    --gold: #b39b80;
    --rule: rgba(255,255,255,0.45);
  }
  * { margin: 0; padding: 0; box-sizing: border-box; }
  html, body { width: 1200px; height: 1200px; overflow: hidden; background: var(--page); }
  .poster {
    position: absolute; left: 210px; top: 48px; width: 788px; height: 1113px;
    background: radial-gradient(ellipse at 55% 40%, var(--ink-soft) 0%, var(--ink) 75%);
    overflow: hidden; color: var(--text); font-family: "Poppins", sans-serif;
  }
  .partner-note { position: absolute; left: 56px; top: 82px; font-size: 21px; line-height: 27px; font-weight: 400; }
  .partner-name { position: absolute; left: 56px; top: 160px; font-size: 50px; font-weight: 500; letter-spacing: 0.5px; }
  .rule { position: absolute; left: 56px; width: 419px; height: 1px; background: var(--rule); }
  .rule.top { top: 278px; }
  .rule.bottom { top: 584px; }
  .event-title { font-weight: inherit; }
  .title-lead { position: absolute; left: 52px; top: 308px; font-family: "Jost", sans-serif; font-size: 58px; font-weight: 400; line-height: 1; }
  .title-main { position: absolute; left: 52px; top: 360px; font-family: "Cormorant Garamond", serif; font-size: 112px; font-weight: 500; line-height: 1; color: var(--gold); letter-spacing: -2px; transform: scaleX(0.87); transform-origin: left; }
  .title-year { position: absolute; left: 52px; top: 448px; font-family: "Cormorant Garamond", serif; font-size: 124px; font-weight: 500; line-height: 1; color: var(--gold); font-variant-numeric: lining-nums; }
  .host-mark { position: absolute; left: 48px; top: 614px; width: 118px; height: 118px; border: 2px solid var(--text); border-radius: 50%; display: flex; align-items: center; justify-content: center; font-size: 21px; font-weight: 600; }
  .host-line { position: absolute; left: 204px; top: 612px; font-size: 24px; line-height: 31px; font-weight: 400; }
  .host-line .band { color: var(--gold); font-weight: 700; }
  .bbq { position: absolute; left: 56px; top: 753px; font-size: 18.5px; line-height: 23px; font-weight: 400; }
  .address-box { position: absolute; left: 56px; top: 817px; width: 353px; height: 41px; border: 1.5px solid var(--text); display: flex; align-items: center; justify-content: center; color: var(--gold); font-size: 22px; font-weight: 600; }
  .contact { position: absolute; left: 56px; display: flex; align-items: center; gap: 16px; font-size: 17.5px; font-weight: 700; line-height: 22px; }
  .contact .icon { width: 37px; height: 37px; border-radius: 50%; background: var(--gold); display: flex; align-items: center; justify-content: center; flex: none; }
  .contact .hl { color: var(--gold); }
  .contact.place { top: 878px; }
  .contact.phone { top: 930px; }
  .contact.mail { top: 974px; }
  .guitar-photo {
    position: absolute; left: 424px; top: 92px; width: 222px; height: 928px;
    background:
      radial-gradient(ellipse 70% 30% at 55% 72%, rgba(235,235,235,0.28) 0%, rgba(40,40,40,0.35) 55%, rgba(12,12,12,0) 100%),
      radial-gradient(ellipse 30% 55% at 60% 30%, rgba(140,110,80,0.35) 0%, rgba(12,12,12,0) 100%);
  }
  .band-vertical { position: absolute; left: 648px; top: 100px; }
</style>
</head>
<body>
<main class="poster">
  <p class="partner-note">Cet événement est organisé en<br>collaboration avec LE BRUMAIRE</p>
  <p class="partner-name">Le Brumaire</p>
  <div class="rule top"></div>

  <h1 class="event-title">
    <span class="title-lead">FÊTE DE LA</span>
    <span class="title-main">MUSIQUE</span>
    <span class="title-year">2023</span>
  </h1>
  <div class="rule bottom"></div>

  <div class="host-mark">L'Escale</div>
  <p class="host-line">L'Escale, réunit le<br>groupe<br><span class="band">VELMORANTE</span><br>sur sa terrasse</p>
  <p class="bbq">Nous organisons un barbecue géant<br>à cette occasion.</p>

  <div class="address-box">Adresse de l'événement</div>

  <div class="contact place">
    <span class="icon"><svg width="16" height="20" viewBox="0 0 16 20"><path d="M8 0C3.6 0 0 3.5 0 7.8 0 13.5 8 20 8 20s8-6.5 8-12.2C16 3.5 12.4 0 8 0z" fill="#0c0c0c"/><circle cx="8" cy="7.8" r="3" fill="#b39b80"/></svg></span>
    <span>12-16 Rue Fernand Lavigne à<br>CAMBRAI. <span class="hl">4 A partir de 19h.</span></span>
  </div>
  <div class="contact phone">
    <span class="icon"><svg width="18" height="18" viewBox="0 0 24 24"><path d="M6.6 10.8c1.4 2.8 3.8 5.1 6.6 6.6l2.2-2.2c.3-.3.7-.4 1-.2 1.1.4 2.3.6 3.6.6.6 0 1 .4 1 1V20c0 .6-.4 1-1 1C10.6 21 3 13.4 3 4c0-.6.4-1 1-1h3.5c.6 0 1 .4 1 1 0 1.3.2 2.5.6 3.6.1.3 0 .7-.2 1l-2.3 2.2z" fill="#0c0c0c"/></svg></span>
    <span>03 41 58 62 19</span>
  </div>
  <div class="contact mail">
    <span class="icon"><svg width="20" height="14" viewBox="0 0 20 14"><rect x="0.75" y="0.75" width="18.5" height="12.5" fill="none" stroke="#0c0c0c" stroke-width="1.5"/><path d="M1 1l9 7 9-7M1 13l6.5-6M19 13l-6.5-6" fill="none" stroke="#0c0c0c" stroke-width="1.5"/></svg></span>
    <span>marc@orvaline-habitat.example</span>
  </div>

  <div class="guitar-photo" role="img" aria-label="Photographie d'une guitare électrique noire à plaque blanche, debout, avec son reflet au sol"></div>

  <svg class="band-vertical" width="90" height="590" viewBox="0 0 90 590" aria-hidden="true">
    <text transform="translate(80 580) rotate(-90)" textLength="572" lengthAdjust="spacingAndGlyphs" font-family="Poppins, sans-serif" font-size="90" font-weight="500" fill="none" stroke="rgba(255,255,255,0.85)" stroke-width="1.6">VELMORANTE</text>
  </svg>
</main>
</body>
</html>
```